House Cleaning Platform for Consumers and Cleaners

UPDATE: I've attached screenshots showing a purchase flow example, something all designers have missed in their designs. PLEASE check the URLs I've included in the brief for examples of a cleaning website. I've seen mostly landing pages and nothing else.

WHAT I'M LOOKING FOR:
I need the UI designed for a house cleaning web platform from 2 separate experiences: one from the consumer end to order a cleaner to come clean their house and one from a cleaner’s end that manages their orders and manages their schedule.

The UI will need to include photo uploading for before and after photos, a checkout/cart experience w/ tips, toggle options for adding and removing rooms/extras cleaning add-ons, customer+cleaner reviews (meaning the cleaner finished the job and they can rate and review the customer as well as the customer can rate and review the cleaner), order history for consumers, job history for cleaners, profile, settings, and landing pages for both.

PLEASE DO NOT USE THE COLOR BLUE AS THE PRIMARY COLOR. Use a light green (HEX #2fdf86) instead for primary theming color.

REFERENCES:
If you'd like a few websites I've enjoyed for references, checkout:
larkpolish.example, vomby.example, and brightfernhome.example.

For sake of branding, the company name is PlumNest. Currently do not have a logo as we have not decided on the name. Logo will come later.

Feel free to reach out to me if you have any questions!
Updates

Most designer submissions were a landing page and only a landing page. Very few designed the flows I requested and none designed a schedule management page. I even updated the Brief to more clearly outline the needs and references. Only about 2-3 of the designers actually did more than a landing page. Still don't believe I received 6 designers input that I had paid for.

Target Market(s)

FULL-TIME WORKING HOUSEHOLDS, SINGLE PROFESSIONALS, SINGLE PARENTS, ELDERLY & MOBILITY CHALLENGED, BUSY BODIES.

Industry/Entity Type

Cleaning, gig work.

Number of Pages Required

5+ page

Font styles to use
Other font styles liked:
• Jost or Lexend are great Google Font options I've used in the pitch deck and horribly done app mockups.

Colors
00AB8E
00BBA5
67D7C9
C6EFE9
E9F9F6
59FF00
82FF00
B8FF75
E3FFCB
F4FFEA
FFF300
FFF600
FEFA6F
FFFEC7
FFFEE8
FFC000
F8CF3A
FAE287
FDF2CF
FEFAEE

Requirements
Must have
• Landing page, consumer flow, cleaner schedule management, checkout flow, Rate & Review for consumer and/or cleaner, order history, profile.
Nice to have
• I'd like it to be simple in design and modern, but not so simple it's boring. Iconography can sometimes break that up, but I don't want it looking busy. It's a cleaning platform so the UI should look clean.

```html
<!DOCTYPE html>
<html lang="en">
<head>
<meta charset="UTF-8">
<title>PlumNest – Book Your Services Now</title>
<link href="https://fonts.googleapis.com/css2?family=Open+Sans:wght@600;700&family=Nunito:wght@400;500;600&display=swap" rel="stylesheet">
<style>
  :root {
    --brand-green: #27d17f;
    --brand-orange: #f7931e;
    --ink: #111111;
    --body-text: #3a3a3a;
    --placeholder: #a8a8a8;
    --field-border: #cfcfcf;
    --radio-border: #c8c8c8;
    --page-bg: #ffffff;
  }
  * { box-sizing: border-box; margin: 0; padding: 0; }
  html, body {
    width: 1200px; height: 959px; overflow: hidden;
    background: var(--page-bg);
    font-family: 'Nunito', sans-serif;
    color: var(--ink);
  }
  .page { position: relative; width: 1200px; height: 959px; }

  /* Header */
  .brand {
    position: absolute; left: 101px; top: 18px;
    font-family: 'Open Sans', sans-serif; font-weight: 700;
    font-size: 32px; line-height: 40px; color: var(--brand-green);
    letter-spacing: -0.5px;
  }
  .main-nav {
    position: absolute; left: 438px; top: 26px;
    display: flex; gap: 19px;
    font-size: 11.5px; font-weight: 500; line-height: 18px;
  }
  .search-box {
    position: absolute; left: 731px; top: 22.5px;
    width: 218px; height: 25px;
    border: 1px solid var(--field-border); border-radius: 13px;
    display: flex; align-items: center; padding-left: 7px; gap: 14px;
    font-size: 11.5px; font-weight: 500; color: var(--ink);
  }
  .login-link {
    position: absolute; left: 981px; top: 26px;
    font-size: 11.5px; font-weight: 500; line-height: 18px;
  }
  .signup-btn {
    position: absolute; left: 1024px; top: 22.5px;
    width: 74px; height: 25px; border-radius: 13px;
    background: var(--brand-green);
    font-size: 10.5px; font-weight: 600;
    display: flex; align-items: center; justify-content: center;
  }

  /* Title */
  .page-title {
    position: absolute; left: 0; right: 0; top: 128px;
    text-align: center;
    font-family: 'Open Sans', sans-serif; font-weight: 700;
    font-size: 37px; line-height: 46px;
  }
  .title-rule {
    position: absolute; left: 0; right: 0; top: 215px;
    height: 1px; background: var(--brand-green);
  }

  /* Form blocks */
  .field-block { position: absolute; width: 469px; }
  .field-block h2 {
    font-family: 'Open Sans', sans-serif; font-weight: 600;
    font-size: 20px; line-height: 26px;
  }
  .field-block p {
    margin-top: 12px;
    font-size: 11.5px; line-height: 18px; color: var(--body-text);
  }
  .field-block p strong { font-weight: 600; color: var(--ink); }
  .text-input {
    margin-top: 14px; height: 37px; width: 100%;
    border: 1px solid var(--field-border); border-radius: 2px;
    padding: 0 19px; display: flex; align-items: center; justify-content: space-between;
    font-size: 11.5px; color: var(--placeholder);
  }
  .zip-block { left: 101px; top: 281px; }
  .sqft-block { left: 630px; top: 281px; }
  .bed-block { left: 101px; top: 448px; }
  .bath-block { left: 630px; top: 448px; }
  .pets-block { left: 101px; top: 633px; width: 700px; }

  .pet-options {
    position: absolute; top: 709px; left: 101px;
    font-size: 11.5px; font-weight: 500; line-height: 18px;
  }
  .pet-option { position: absolute; display: flex; align-items: center; gap: 13px; white-space: nowrap; }
  .radio {
    width: 12px; height: 12px; border-radius: 50%;
    border: 1px solid var(--radio-border); flex: none;
  }
  .radio.checked { border: 3.5px solid var(--brand-green); }

  /* Actions */
  .btn {
    position: absolute; top: 790px; width: 175px; height: 50px; border-radius: 25px;
    display: flex; align-items: center; justify-content: center;
    font-size: 15px; font-weight: 600;
  }
  .btn-back { left: 101px; border: 1px solid var(--field-border); }
  .btn-next { left: 307.5px; background: var(--brand-green); }
</style>
</head>
<body>
<div class="page">
  <header>
    <div class="brand">PlumNest</div>
    <nav class="main-nav">
      <span>Home</span><span>Pricing</span><span>Services</span><span>Contact</span><span>Help</span>
    </nav>
    <div class="search-box">
      <svg width="13" height="13" viewBox="0 0 13 13" fill="none" stroke="#111" stroke-width="1.1">
        <circle cx="5.6" cy="5.6" r="4.6"/><line x1="9" y1="9" x2="12.2" y2="12.2"/>
      </svg>
      <span>Search</span>
    </div>
    <span class="login-link">Login</span>
    <span class="signup-btn">Sign Up</span>
  </header>

  <h1 class="page-title">Book Your Services Now</h1>
  <div class="title-rule"></div>

  <section class="field-block zip-block">
    <h2>Enter Property Zip Code</h2>
    <p>The zip code helps us to pull accurate quote and pricing details.</p>
    <div class="text-input">Zip Code</div>
  </section>

  <section class="field-block sqft-block">
    <h2>Total Square Feet At Home</h2>
    <p>Enter your total square feet of your home. This number will be verified by our system.</p>
    <div class="text-input">Square Footage</div>
  </section>

  <section class="field-block bed-block">
    <h2>How Many Bedrooms?</h2>
    <p>Enter total number of bedrooms in the home. You can Exclude number of Bedrooms at a later step.</p>
    <div class="text-input">Select Bedrooms
      <svg width="12" height="7" viewBox="0 0 12 7"><path d="M0 0h12L6 7z" fill="#111"/></svg>
    </div>
  </section>

  <section class="field-block bath-block">
    <h2>How Many Bathrooms?</h2>
    <p>Enter total number of bathrooms in the home. <strong>Round half baths up</strong> (this will not affect price). You can Exclude Bedrooms at a later step.</p>
    <div class="text-input">Select Bathhrooms
      <svg width="12" height="7" viewBox="0 0 12 7"><path d="M0 0h12L6 7z" fill="#111"/></svg>
    </div>
  </section>

  <section class="field-block pets-block">
    <h2>Any Pets At Home?</h2>
    <p>This include any cats or dogs that live in or spend time in the same home. Select any one.</p>
  </section>

  <div class="pet-options">
    <label class="pet-option" style="left:0"><span class="radio checked"></span>No pets in the home</label>
    <label class="pet-option" style="left:198px"><span class="radio"></span>Dog(s)</label>
    <label class="pet-option" style="left:320px"><span class="radio"></span>Cats(s)</label>
    <label class="pet-option" style="left:444px"><span class="radio"></span>Dog(s) and Cats(s)</label>
  </div>

  <span class="btn btn-back">Back</span>
  <span class="btn btn-next">Save &amp; Next</span>
</div>
</body>
</html>
```